Brightfield Ventures Inc. Letterhead

Creation of attractive and eye catching letterhead for a business start-up for the construction industry. Letterhead must relate to construction, but avoid standard hammer and tools in the design.

I forgot to add some details, sorry about that. Some pertinent info: Ph: 916-555-0187 brightfieldventures.example 448 Willowmere Ave, Ste 210 Folsom, CA 95999 info@brightfieldventures.example not sure if slogan should be in there" “Connecting construction professionals to create a purpose driven industry.” must be able to be used in word. Thanks!

```html
<!DOCTYPE html>
<html lang="en">
<head>
<meta charset="utf-8">
<title>Brightfield Ventures Inc. Letterhead</title>
<link rel="stylesheet" href="https://fonts.googleapis.com/css2?family=Lato:wght@400;700&family=Kaushan+Script&display=swap">
<style>
  :root {
    --navy: #1c1f54;
    --red: #d21f26;
    --text: #555558;
    --muted: #4a4a4e;
    --paper: #ffffff;
    --rule: #c9c9cf;
  }
  * { box-sizing: border-box; margin: 0; padding: 0; }
  html, body { width: 897px; height: 1200px; overflow: hidden; background: var(--paper); }
  .letterhead {
    position: relative;
    width: 897px;
    height: 1200px;
    background: var(--paper);
    font-family: "Lato", sans-serif;
    color: var(--text);
  }
  .brand {
    position: absolute;
    left: 75px;
    top: 96px;
    display: flex;
    align-items: center;
    gap: 10px;
  }
  .brand-mark { width: 18px; height: 18px; background: var(--red); }
  .brand-name {
    font-family: "Lato", sans-serif;
    font-weight: 700;
    font-size: 22px;
    letter-spacing: 0.5px;
    color: var(--navy);
  }
  .contact {
    position: absolute;
    right: 80px;
    top: 62px;
    padding-left: 12px;
    border-left: 1px solid var(--rule);
    font-size: 13px;
    line-height: 19px;
    color: var(--muted);
    list-style: none;
  }
  .contact li { display: flex; align-items: center; gap: 5px; }
  .contact svg { width: 10px; height: 10px; fill: var(--red); flex: none; }
  .letter {
    position: absolute;
    left: 75px;
    right: 80px;
    top: 308px;
  }
  .salutation {
    font-weight: 700;
    font-size: 16px;
    color: var(--navy);
    margin-bottom: 22px;
  }
  .letter p.body {
    font-size: 16.4px;
    line-height: 27.5px;
    text-align: justify;
    hyphens: auto;
    margin-bottom: 20px;
  }
  .closing {
    font-size: 19px;
    color: #222;
    margin-top: 28px;
  }
  .signature {
    font-family: "Kaushan Script", cursive;
    font-size: 30px;
    color: var(--navy);
    margin-top: 4px;
  }
  .footer { position: absolute; left: 0; right: 0; top: 1112px; }
  .footer .line { height: 2px; background: var(--red); }
  .footer .band {
    margin-top: 6px;
    height: 40px;
    background: var(--navy);
    color: #fff;
    font-size: 13px;
    display: flex;
    align-items: center;
    justify-content: center;
    gap: 5px;
  }
  .footer .band svg { width: 10px; height: 12px; fill: #fff; }
  .footer .line.low { margin-top: 6px; }
  .footer .line.lowest { margin-top: 4px; }
</style>
</head>
<body>
<main class="letterhead">
  <header>
    <div class="brand">
      <span class="brand-mark"></span>
      <span class="brand-name">Brightfield Ventures Inc.</span>
    </div>
    <ul class="contact">
      <li><svg viewBox="0 0 10 10"><path d="M2 0.5l2 2-1 1.2c.6 1.3 1.6 2.3 2.9 2.9L7 5.6l2 2-1.2 1.6C4.5 9 1 5.5.8 2.2z"/></svg>916-555-0187</li>
      <li><svg viewBox="0 0 10 10"><path d="M0 2h10v1L5 6 0 3zM0 4l5 3 5-3v5H0z"/></svg>info@brightfieldventures.example</li>
      <li><svg viewBox="0 0 10 10"><circle cx="5" cy="5" r="4.3" fill="none" stroke="#d21f26" stroke-width="1.2"/><path d="M0.7 5h8.6M5 .7v8.6" stroke="#d21f26" stroke-width="1"/></svg>www.brightfieldventures.example</li>
    </ul>
  </header>

  <section class="letter">
    <p class="salutation">Dear Mr. Lorem,</p>
    <p class="body">Lorem ipsum dolor sit amet, consectetuer adipiscing elit, sed diam nonummy nibh euismod tincidunt ut laoreet dolore magna aliquam erat volutpat. Ut wisi enim ad minim veniam, quis nostrud exerci tation ullamcorper suscipit lobortis nisl ut aliquip ex ea commodo consequat. Duis autem vel eum iriure dolor in hendiusto odio dignissim qui blandit praesent luptatum zzril delenit augue duis dolore te feugait nulla facilisi.</p>
    <p class="body">Lorem ipsum dolor sit amet, consectetuer adipiscing elit, sed diam nonummy nibh euismod tincidunt ut laoreet dolore magna aliquam erat volutpat. Ut wisi enim ad minim veniam, quis nostrud exerci tation ullamcorper suscipit lobortis nisl ut aliquip ex ea commodo consequat. Duis autem vel eum iriure dolor in hendiusto odio dignissim qui blandit praesent luptatum zzril delenit augue duis dolore te feugait nulla facilisi.</p>
    <p class="body">Lorem ipsum dolor sit amet, consectetuer adipiscing elit, sed diam nonummy nibh euismod tincidunt ut laoreet dolore magna aliquam erat volutpat. Ut wisi enim ad minim veniam, quis nostrud exerci tation ullamcorper suscipit lobortis nisl ut aliquip ex ea commodo consequat. Duis autem vel eum iriure dolor in hendiusto odio dignissim qui blandit praesent luptatum zzril delenit augue duis dolore te feugait nulla facilisi.</p>
    <p class="closing">Sincerely Your,</p>
    <p class="signature">Your Name</p>
  </section>

  <footer class="footer">
    <div class="line"></div>
    <div class="band">
      <svg viewBox="0 0 10 12"><path d="M5 0a4 4 0 0 0-4 4c0 3 4 8 4 8s4-5 4-8a4 4 0 0 0-4-4zm0 5.6A1.6 1.6 0 1 1 5 2.4a1.6 1.6 0 0 1 0 3.2z"/></svg>
      448 Willowmere Ave, Ste 210, Folsom, CA 95999
    </div>
    <div class="line low"></div>
    <div class="line lowest"></div>
  </footer>
</main>
</body>
</html>
```